Vantoq Business Card Project showing the logo and a marbo image on the rear

Design a whacky but professional business card, the logo is for the front and the Marbo image is for the rear. Happy to consider other open source Marbo Images if the designer wants to select one from the web. Vantoq is a competitor to OMB.com.au and Pellory.com.au and is based around every property in Australia

Target Market(s)

Business

Contact Information for Business Card

Name, Title, Email, Web, Phone Number

Font styles to use
Other font styles liked:
• avenir

Requirements
Must have
• Image on Back logo on front
Nice to have
• Happy to consider other images on rear, preftably Colin Marbo. Image supplied I own, we can use open source other Marbo Images

```html
<!DOCTYPE html>
<html lang="en">
<head>
<meta charset="UTF-8">
<title>Vantoq Business Card</title>
<link rel="stylesheet" href="https://fonts.googleapis.com/css2?family=Montserrat:wght@700&family=Roboto:wght@400&family=Jost:wght@600&display=swap">
<style>
  :root {
    --page-bg: #e9e6e4;
    --card-orange: #ff8c00;
    --ink: #111111;
    --window-light: #f7f5f5;
    --window-mid: #e2dcdc;
    --window-edge: #cfc7c8;
  }
  html, body {
    margin: 0;
    padding: 0;
    width: 1200px;
    height: 900px;
    overflow: hidden;
    background: var(--page-bg);
  }
  .business-card {
    position: absolute;
    left: 120px;
    top: 153px;
    width: 960px;
    height: 594px;
    background: var(--card-orange);
    color: var(--ink);
    box-shadow: 0 10px 30px rgba(0,0,0,0.12);
  }
  .holder-name {
    position: absolute;
    left: 47px;
    top: 96px;
    margin: 0;
    font-family: "Montserrat", sans-serif;
    font-weight: 700;
    font-size: 36px;
    letter-spacing: -0.5px;
    line-height: 1;
  }
  .holder-title {
    position: absolute;
    left: 47px;
    top: 135px;
    margin: 0;
    font-family: "Roboto", sans-serif;
    font-size: 29px;
    line-height: 1;
  }
  .contact-list {
    position: absolute;
    left: 47px;
    top: 369px;
    margin: 0;
    padding: 0;
    list-style: none;
    font-family: "Roboto", sans-serif;
    font-size: 28.5px;
    line-height: 37px;
  }
  .contact-item {
    display: flex;
    align-items: center;
    gap: 9px;
  }
  .contact-icon {
    width: 29px;
    height: 29px;
    flex: none;
  }
  .brand-window {
    position: absolute;
    left: 396px;
    top: 41px;
    width: 512px;
    height: 512px;
    border-radius: 50%;
    background: radial-gradient(circle at 55% 40%, var(--window-light) 0%, var(--window-mid) 65%, var(--window-edge) 100%);
  }
  .brand-mark {
    position: absolute;
    left: 438px;
    top: 232px;
    width: 86px;
    height: 86px;
    background: var(--card-orange);
  }
  .brand-name {
    position: absolute;
    left: 560px;
    top: 240px;
    margin: 0;
    font-family: "Jost", sans-serif;
    font-weight: 600;
    font-size: 96px;
    line-height: 1;
    color: var(--ink);
  }
</style>
</head>
<body>
  <div class="business-card">
    <h1 class="holder-name">PETER HALVERD</h1>
    <p class="holder-title">Managing Director</p>

    <ul class="contact-list">
      <li class="contact-item">
        <svg class="contact-icon" viewBox="0 0 24 24" aria-hidden="true">
          <path d="M6.6 3.5l3 3.2-1.8 2.2c1.2 2.6 3.3 4.7 5.8 5.9l2.2-1.8 3.2 3-1.6 3.2c-7.4-.6-13.2-6.5-13.8-13.9z" fill="none" stroke="#111" stroke-width="2" stroke-linejoin="round"/>
          <path d="M14 3.5a6.5 6.5 0 0 1 6.5 6.5M14 7a3 3 0 0 1 3 3" fill="none" stroke="#111" stroke-width="1.8" stroke-linecap="round"/>
        </svg>
        <span>044-287 310 564</span>
      </li>
      <li class="contact-item">
        <svg class="contact-icon" viewBox="0 0 24 24" aria-hidden="true">
          <rect x="2" y="5" width="20" height="14" fill="#111"/>
          <path d="M2.5 5.5L12 13l9.5-7.5M2.5 18.5l7-6.5M21.5 18.5l-7-6.5" fill="none" stroke="#ff8c00" stroke-width="1.5"/>
        </svg>
        <span>hello@vantoqmail.com</span>
      </li>
      <li class="contact-item">
        <svg class="contact-icon" viewBox="0 0 24 24" aria-hidden="true">
          <g fill="none" stroke="#111" stroke-width="1.6">
            <circle cx="12" cy="12" r="9.5"/>
            <ellipse cx="12" cy="12" rx="4.2" ry="9.5"/>
            <path d="M12 2.5v19M2.5 12h19M4 7h16M4 17h16"/>
          </g>
        </svg>
        <span>www.vantoqhomes.com</span>
      </li>
    </ul>

    <div class="brand-window"></div>
    <div class="brand-mark"></div>
    <p class="brand-name">Vantoq</p>
  </div>
</body>
</html>
```